PlayTallyCollective - Game Statistics and Achievement Tracking

I need a new modern design for an existing website.

The website is a project to track statistics and achievements for games (currently Vaporn Achievements/Stats and stats for Cargo Haul Odyssey 2 and Frontier Rig Journeys).
I am currently expanding the site with other platforms (like QVR) and more games.
I am also adding a user registration/signin with user profiles to show off their achievements and stats across all platforms and games.

The current website is available at https://plytly.example/
To search for data you can use the username "pixelornin" (without quotes).

The design should be modern and extendable and contain space for a logo.

The logo should match the project. It should combine Gaming with statistics.

Target Market(s)

Video game players

Number of Pages Required

5+ page

Font styles to use
Sans Serif

Requirements
Must have
• Basic Layout, User profile page (not yet available on live site), Search Page for Platforms/Games, Platform profile page, Dark theme

```html
<!DOCTYPE html>
<html lang="en">
<head>
<meta charset="utf-8">
<title>PlayTallyCollective – Profile</title>
<link href="https://fonts.googleapis.com/css2?family=Noto+Sans:wght@400;600;700&display=swap" rel="stylesheet">
<style>
:root{
  --bg:#0b0d10;
  --header:#111317;
  --panel:rgba(18,20,24,0.94);
  --card:#15171b;
  --line:#2c2f35;
  --accent:#1ea3d6;
  --text:#eceef0;
  --muted:#9aa0a6;
  --footer:#050607;
}
*{box-sizing:border-box;margin:0;padding:0}
html,body{width:1200px;height:675px;overflow:hidden}
body{font-family:"Noto Sans",sans-serif;color:var(--text);background:var(--bg);position:relative}
.backdrop{position:absolute;inset:0;background:radial-gradient(ellipse at 50% 55%,#3a2c26 0%,#1d1a1c 45%,#0b0d10 80%)}
.site-header{position:absolute;left:0;top:0;width:1200px;height:76px;background:var(--header);border-bottom:1px solid #24272c;border-radius:0 0 14px 14px}
.brand{position:absolute;left:38px;top:26px;display:flex;align-items:center;gap:7px;font-size:12px;font-weight:600;color:var(--accent)}
.brand-dot{width:18px;height:18px;border-radius:50%;background:var(--accent)}
.main-nav{position:absolute;left:396px;top:0;height:76px;display:flex;gap:36px;align-items:center;font-size:10px;color:var(--muted)}
.main-nav a{display:flex;align-items:center;gap:7px;color:inherit;text-decoration:none;height:76px;position:relative}
.main-nav a.active{color:var(--text)}
.main-nav a.active::after{content:"";position:absolute;left:-8px;right:-8px;bottom:1px;height:3px;border-radius:2px;background:var(--accent)}
.user-menu{position:absolute;right:20px;top:28px;display:flex;align-items:center;gap:6px;font-size:10px}
.user-avatar{width:20px;height:20px;border-radius:50%;background:linear-gradient(135deg,#2f8fd0,#c79a5a)}
.profile-panel{position:absolute;left:126px;top:116px;width:949px;height:198px;background:var(--panel);border:1px solid #26292e;border-radius:16px}
.avatar{position:absolute;left:40px;top:14px;width:136px;height:136px;border-radius:50%;background:radial-gradient(circle at 50% 40%,#6fc4ef,#1b6fa8 70%);border:3px solid #0f4e7a}
.profile-name{position:absolute;left:0;width:215px;top:160px;text-align:center;font-size:13px;font-weight:600}
.divider{position:absolute;left:214px;top:17px;width:1px;height:162px;background:var(--line)}
.collapse{position:absolute;right:28px;top:25px;width:14px;height:1px;background:var(--text)}
.stat{position:absolute;font-size:8.5px;display:flex;align-items:center;gap:4px}
.stat svg{width:10px;height:10px;stroke:var(--muted);fill:none;stroke-width:1.3}
.stat-value{position:absolute;font-size:8.5px;color:var(--muted)}
.jobs-panel{position:absolute;left:126px;top:326px;width:949px;height:275px;background:rgba(18,20,24,0.7);border-radius:16px 16px 0 0;overflow:hidden}
.job-card{position:absolute;width:217px;height:222px;background:var(--card);border:1px solid #2a2d32;border-radius:10px}
.job-card.selected{background:var(--accent);border-color:var(--accent)}
.job-title{height:37px;padding:11px 18px 0;font-size:11px;font-weight:700;border-bottom:1px solid var(--line)}
.selected .job-title{border-color:rgba(255,255,255,0.25)}
.job-meta{display:flex;justify-content:space-between;padding:10px 18px 0}
.job-meta small{display:block;font-size:6px;color:var(--muted)}
.job-meta span{font-size:9.5px}
.job-meta div:last-child{text-align:right}
.selected .job-meta small{color:rgba(255,255,255,0.55)}
.place{display:flex;gap:4px;padding:0 18px;font-size:9.5px;line-height:15px;color:#d3d6da}
.place svg{width:9px;height:9px;margin-top:3px;stroke:currentColor;fill:none;stroke-width:1.4;flex:none}
.from{margin-top:25px}.to{margin-top:10px}
.job-stats{position:absolute;left:18px;right:18px;bottom:18px;display:flex;justify-content:space-between;font-size:11px;color:#d3d6da}
.job-stats span{display:flex;align-items:center;gap:3px}
.job-stats svg{width:10px;height:10px;stroke:currentColor;fill:none;stroke-width:1.4}
.selected .place,.selected .job-stats{color:#fff}
.site-footer{position:absolute;left:0;bottom:0;width:1200px;height:33px;background:var(--footer);display:flex;align-items:center;justify-content:space-between;padding:0 16px;font-size:10px}
</style>
</head>
<body>
<div class="backdrop" role="img" aria-label="Dimmed night city street scene from a trucking game"></div>

<header class="site-header">
  <div class="brand"><span class="brand-dot"></span>PlayTallyCollective</div>
  <nav class="main-nav">
    <a href="#"><svg width="12" height="12" viewBox="0 0 12 12" fill="none" stroke="#9aa0a6" stroke-width="1.2"><path d="M2 5.5 6 2l4 3.5V11H2z"/></svg>Home</a>
    <a href="#"><svg width="12" height="12"><circle cx="6" cy="6" r="5.5" fill="#2a8fd0"/></svg>Vaporn</a>
    <a href="#" class="active"><svg width="12" height="12"><circle cx="6" cy="6" r="5.5" fill="#e0a93a"/></svg>Games ⌄</a>
    <a href="#"><svg width="12" height="12" viewBox="0 0 12 12" fill="none" stroke="#9aa0a6" stroke-width="1.1"><circle cx="6" cy="6" r="5"/><path d="M6 5.2V9M6 3.3v.6"/></svg>About us ⌄</a>
  </nav>
  <div class="user-menu"><span class="user-avatar"></span>pixelornin ⌄</div>
</header>

<section class="profile-panel">
  <div class="avatar" role="img" aria-label="Cartoon profile avatar of the player"></div>
  <div class="profile-name">pixelornin</div>
  <div class="divider"></div>
  <div class="collapse"></div>

  <div class="stat" style="left:248px;top:33px"><svg viewBox="0 0 10 10"><path d="M5 1 9 3v4L5 9 1 7V3z"/></svg>Jobs Completed</div><div class="stat-value" style="left:371px;top:33px">140</div>
  <div class="stat" style="left:248px;top:63px"><svg viewBox="0 0 10 10"><circle cx="5" cy="5" r="4"/><path d="M5 3v2l1.5 1"/></svg>Total Time:</div><div class="stat-value" style="left:367px;top:64px">2d 18h 58m</div>
  <div class="stat" style="left:248px;top:93px"><svg viewBox="0 0 10 10"><circle cx="3" cy="7" r="2"/><circle cx="7.5" cy="2.5" r="1.5"/></svg>Total Distance:</div><div class="stat-value" style="left:371px;top:93px">36.286,57mi</div>
  <div class="stat" style="left:248px;top:123px"><svg viewBox="0 0 10 10"><rect x="1" y="2.5" width="8" height="5"/></svg>Total Revenue:</div><div class="stat-value" style="left:371px;top:123px">US$ 1.745.094</div>
  <div class="stat" style="left:248px;top:153px"><svg viewBox="0 0 10 10"><path d="M5 1v8M2 3h6M1 6l1-3 1 3zM7 6l1-3 1 3z"/></svg>Fines Paid:</div><div class="stat-value" style="left:371px;top:153px">141</div>

  <div class="stat" style="left:480px;top:33px"><svg viewBox="0 0 10 10"><rect x="1" y="2" width="8" height="6"/><path d="M3 2v6M7 2v6"/></svg>Tollgates Passed:</div><div class="stat-value" style="left:604px;top:33px">2</div>
  <div class="stat" style="left:480px;top:63px"><svg viewBox="0 0 10 10"><path d="M1 7h8L8 9H2zM3 7V4h4v3M5 4V1"/></svg>Transportations used:</div><div class="stat-value" style="left:604px;top:63px">0</div>
  <div class="stat" style="left:480px;top:93px"><svg viewBox="0 0 10 10"><circle cx="5" cy="4" r="3"/><path d="M3 7l-1 2.5M7 7l1 2.5"/></svg>Total Experience:</div><div class="stat-value" style="left:604px;top:93px">78685</div>
  <div class="stat" style="left:480px;top:123px"><svg viewBox="0 0 10 10"><circle cx="5" cy="5" r="4"/><path d="M5 3v2l1.5 1"/></svg>Total In-Game Time:</div><div class="stat-value" style="left:604px;top:123px">66d 9h 46m</div>
  <div class="stat" style="left:480px;top:153px"><svg viewBox="0 0 10 10"><rect x="1.5" y="1.5" width="7" height="7" rx="1"/></svg>Total Mass:</div><div class="stat-value" style="left:604px;top:153px">2674t</div>

  <div class="stat" style="left:712px;top:33px"><svg viewBox="0 0 10 10"><rect x="1" y="2" width="6" height="5"/><path d="M7 4h2v3H7"/></svg>Trucks driven:</div><div class="stat-value" style="left:836px;top:33px">8</div>
  <div class="stat" style="left:712px;top:63px"><svg viewBox="0 0 10 10"><path d="M5 1v8M2 3h6M1 6l1-3 1 3zM7 6l1-3 1 3z"/></svg>Total fines:</div><div class="stat-value" style="left:836px;top:63px">US$ 118.660</div>
  <div class="stat" style="left:712px;top:93px"><svg viewBox="0 0 10 10"><circle cx="5" cy="5" r="4"/><circle cx="5" cy="5" r="2"/></svg>Total toll paid:</div><div class="stat-value" style="left:836px;top:93px">US$ 50</div>
  <div class="stat" style="left:712px;top:123px"><svg viewBox="0 0 10 10"><rect x="1" y="2" width="8" height="6"/><path d="M1 4h8"/></svg>Paid for transportations:</div><div class="stat-value" style="left:836px;top:123px">US$ 0</div>
</section>

<section class="jobs-panel">
  <article class="job-card" style="left:15px;top:17px">
    <h3 class="job-title">Mountain Fun Gift Packs</h3>
    <div class="job-meta"><div><small>Date</small><span>17.12.2023</span></div><div><small>Time</small><span>05:37</span></div></div>
    <div class="place from"><svg viewBox="0 0 10 10"><path d="M5 9S1.5 5.5 1.5 3.8a3.5 3.5 0 0 1 7 0C8.5 5.5 5 9 5 9z"/><circle cx="5" cy="3.8" r="1.2"/></svg><div>Mountain Resort, Winterland<br>Snowy Peaks</div></div>
    <div class="place to"><svg viewBox="0 0 10 10"><path d="M1.5 9.5V1h6.5l-1.5 2 1.5 2H1.5"/></svg><div>Ardmore,<br>Oklahoma Waldens</div></div>
    <div class="job-stats"><span><svg viewBox="0 0 10 10"><circle cx="5" cy="5" r="4"/><path d="M5 3v2l1.5 1"/></svg>17m</span><span><svg viewBox="0 0 10 10"><circle cx="3" cy="7" r="2"/><circle cx="7.5" cy="2.5" r="1.5"/></svg>101,9mi</span><span><svg viewBox="0 0 10 10"><rect x="1.5" y="1.5" width="7" height="7" rx="1"/></svg>19t</span></div>
  </article>
  <article class="job-card selected" style="left:249px;top:17px">
    <h3 class="job-title">Christmas Handmade Gifts</h3>
    <div class="job-meta"><div><small>Date</small><span>17.12.2023</span></div><div><small>Time</small><span>05:21</span></div></div>
    <div class="place from"><svg viewBox="0 0 10 10"><path d="M5 9S1.5 5.5 1.5 3.8a3.5 3.5 0 0 1 7 0C8.5 5.5 5 9 5 9z"/><circle cx="5" cy="3.8" r="1.2"/></svg><div>Corpus Christi,Texas<br>Home Store</div></div>
    <div class="place to"><svg viewBox="0 0 10 10"><path d="M1.5 9.5V1h6.5l-1.5 2 1.5 2H1.5"/></svg><div>Town Square, Winterland<br>Christmas Market</div></div>
    <div class="job-stats"><span><svg viewBox="0 0 10 10"><circle cx="5" cy="5" r="4"/><path d="M5 3v2l1.5 1"/></svg>14m</span><span><svg viewBox="0 0 10 10"><circle cx="3" cy="7" r="2"/><circle cx="7.5" cy="2.5" r="1.5"/></svg>73,32mi</span><span><svg viewBox="0 0 10 10"><rect x="1.5" y="1.5" width="7" height="7" rx="1"/></svg>19t</span></div>
  </article>
  <article class="job-card" style="left:483px;top:17px">
    <h3 class="job-title">Bulldozer</h3>
    <div class="job-meta"><div><small>Date</small><span>28.05.2023</span></div><div><small>Time</small><span>20:37</span></div></div>
    <div class="place from"><svg viewBox="0 0 10 10"><path d="M5 9S1.5 5.5 1.5 3.8a3.5 3.5 0 0 1 7 0C8.5 5.5 5 9 5 9z"/><circle cx="5" cy="3.8" r="1.2"/></svg><div>Laredo, Texas<br>Deep Wells</div></div>
    <div class="place to"><svg viewBox="0 0 10 10"><path d="M1.5 9.5V1h6.5l-1.5 2 1.5 2H1.5"/></svg><div>Corpus Christi, Texas<br>Tayler Build Works</div></div>
    <div class="job-stats"><span><svg viewBox="0 0 10 10"><circle cx="5" cy="5" r="4"/><path d="M5 3v2l1.5 1"/></svg>23m</span><span><svg viewBox="0 0 10 10"><circle cx="3" cy="7" r="2"/><circle cx="7.5" cy="2.5" r="1.5"/></svg>240,47mi</span><span><svg viewBox="0 0 10 10"><rect x="1.5" y="1.5" width="7" height="7" rx="1"/></svg>18t</span></div>
  </article>
  <article class="job-card" style="left:717px;top:17px">
    <h3 class="job-title">Home Accessories</h3>
    <div class="job-meta"><div><small>Date</small><span>28.05.2023</span></div><div><small>Time</small><span>19:15</span></div></div>
    <div class="place from"><svg viewBox="0 0 10 10"><path d="M5 9S1.5 5.5 1.5 3.8a3.5 3.5 0 0 1 7 0C8.5 5.5 5 9 5 9z"/><circle cx="5" cy="3.8" r="1.2"/></svg><div>Brownsville,<br>Texas Plugged</div></div>
    <div class="place to"><svg viewBox="0 0 10 10"><path d="M1.5 9.5V1h6.5l-1.5 2 1.5 2H1.5"/></svg><div>Laredo, Texas<br>GARC</div></div>
    <div class="job-stats"><span><svg viewBox="0 0 10 10"><circle cx="5" cy="5" r="4"/><path d="M5 3v2l1.5 1"/></svg>24m</span><span><svg viewBox="0 0 10 10"><circle cx="3" cy="7" r="2"/><circle cx="7.5" cy="2.5" r="1.5"/></svg>223,07mi</span><span><svg viewBox="0 0 10 10"><rect x="1.5" y="1.5" width="7" height="7" rx="1"/></svg>19t</span></div>
  </article>

  <article class="job-card" style="left:15px;top:247px"><h3 class="job-title">Ridgeworth Trucks</h3></article>
  <article class="job-card" style="left:249px;top:247px"><h3 class="job-title">Forklifts</h3></article>
  <article class="job-card" style="left:483px;top:247px"><h3 class="job-title">Empty Pallets</h3></article>
  <article class="job-card" style="left:717px;top:247px"><h3 class="job-title">Lift Truck Chassis</h3></article>
</section>

<footer class="site-footer">
  <span>Version: 7.7.0-e6c810c-113</span>
  <span>© Brightquill Studio</span>
  <span>Imprint</span>
</footer>
</body>
</html>
```